HearthMile business card and stationary design

We are looking for a simple yet elegant design for our mortgage company business card and stationary.

The card should include:
Name (Marcus Pell)
Title (CEO)
Phone Number (732-555-0182)
Address (48 Birchwell Court, Suite 314, Fernwick, NJ 07811)
Email (email@hearthmile.example)
"NMLS" i.e. (NMLS 61947)
"Company NMLS" (Company NMLS 274615)

Contact Information for Business Card

See above

```html
<!DOCTYPE html>
<html lang="en">
<head>
<meta charset="utf-8">
<title>HearthMile Business Card</title>
<link rel="stylesheet" href="https://fonts.googleapis.com/css2?family=Montserrat:wght@500;600&family=Arimo:wght@400;700&display=swap">
<style>
  :root {
    --backdrop: #555555;
    --navy: #1a2531;
    --blue: #00aeef;
    --paper: #ffffff;
    --ink: #1a2531;
    --rule: #d6d9dc;
  }
  * { margin: 0; padding: 0; box-sizing: border-box; }
  html, body {
    width: 1065px; height: 1200px; overflow: hidden;
    background: var(--backdrop);
  }
  .canvas { position: relative; width: 1065px; height: 1200px; }

  .card {
    position: absolute;
    width: 583px; height: 363px;
    box-shadow: 3px 3px 4px rgba(0,0,0,0.45);
  }
  .card-front {
    left: 292px; top: 218px;
    background: var(--paper);
    border-radius: 0 182px 182px 0 / 0 182px 182px 0;
  }
  .card-back {
    left: 263px; top: 623px;
    background: var(--navy);
    border-radius: 182px 0 0 182px / 182px 0 0 182px;
  }

  .wordmark {
    position: absolute;
    font-family: "Montserrat", sans-serif;
    font-weight: 500;
    letter-spacing: -0.5px;
    white-space: nowrap;
  }
  .card-front .wordmark {
    left: 37px; top: 162px;
    font-size: 40px; line-height: 56px;
    color: var(--ink);
  }
  .card-back .wordmark {
    left: 34px; right: 0; top: 145px;
    text-align: center;
    font-size: 56px; line-height: 76px;
    color: var(--paper);
  }

  .divider {
    position: absolute;
    left: 291px; top: 105px;
    width: 1px; height: 150px;
    background: var(--rule);
  }

  .identity {
    position: absolute; left: 314px; top: 118px;
    color: var(--ink);
  }
  .person-name {
    font-family: "Montserrat", sans-serif;
    font-weight: 600;
    font-size: 26px; line-height: 30px;
    white-space: nowrap;
  }
  .person-name .surname { color: var(--blue); }
  .person-title {
    font-family: "Arimo", sans-serif;
    font-size: 16.5px; line-height: 18px;
  }
  .contact-list {
    list-style: none;
    margin-top: 13px;
    font-family: "Arimo", sans-serif;
    font-size: 16.5px; line-height: 21.5px;
    white-space: nowrap;
  }
  .contact-label { color: var(--blue); font-weight: 700; margin-right: 3px; }
  .highlight { color: var(--blue); }

  .address {
    position: absolute; left: 97px; top: 302px;
    display: flex; align-items: center; gap: 7px;
    font-family: "Arimo", sans-serif;
    font-size: 15.5px; line-height: 22px;
    color: var(--ink); white-space: nowrap;
  }
  .pin-icon { width: 14px; height: 20px; flex: none; }

  .licenses {
    position: absolute; left: 0; right: 0; top: 301px;
    text-align: center;
    font-family: "Arimo", sans-serif;
    font-size: 17.5px; line-height: 22px;
    color: var(--paper); white-space: nowrap;
  }
  .licenses .label { color: var(--blue); }
  .licenses .sep { margin: 0 9px; }
</style>
</head>
<body>
<main class="canvas">

  <section class="card card-front" aria-label="Business card front">
    <div class="wordmark">HearthMile</div>
    <div class="divider"></div>

    <div class="identity">
      <h1 class="person-name">Marcus <span class="surname">Pell</span></h1>
      <p class="person-title">CEO</p>
      <ul class="contact-list">
        <li><span class="contact-label">T:</span> 732-555-0182</li>
        <li><span class="contact-label">E:</span> email@hearthmile.example</li>
        <li><span class="contact-label">W:</span> www.<span class="highlight">hearthmile</span>.example</li>
      </ul>
    </div>

    <p class="address">
      <svg class="pin-icon" viewBox="0 0 14 20" aria-hidden="true">
        <path d="M7 0C3.1 0 0 3.1 0 7c0 5 7 13 7 13s7-8 7-13c0-3.9-3.1-7-7-7z" fill="#00aeef"/>
        <circle cx="7" cy="6.6" r="2.3" fill="#ffffff"/>
      </svg>
      48 Birchwell Court, Suite 314, Fernwick, NJ 07811
    </p>
  </section>

  <section class="card card-back" aria-label="Business card back">
    <div class="wordmark">HearthMile</div>
    <p class="licenses">
      <span class="label">NMLS</span> 61947<span class="sep">|</span><span class="label">Company NMLS</span> 274615
    </p>
  </section>

</main>
</body>
</html>
```